Modern Business Card

Modern professional business card with more than just logo and demographic info. Something memorable.

We are a trendy/modern chiropractic group with an emphasis on neurology, hence the minimalist-type brain logo. We want to convey that modern and technical aspect with professionalism and the elite nature of our practice environment.

```html
<!DOCTYPE html>
<html lang="en">
<head>
<meta charset="utf-8">
<title>Meridian Spine — Business Card</title>
<link rel="stylesheet" href="https://fonts.googleapis.com/css2?family=EB+Garamond:wght@500&family=Montserrat:wght@400&display=swap">
<style>
  :root {
    --page: #e8e8e8;
    --card: #ffffff;
    --brand-blue: #4a80c1;
    --ink: #222222;
    --muted: #444444;
    --ghost: #f0f0f0;
    --serif: "EB Garamond", Georgia, serif;
    --sans: "Montserrat", Arial, sans-serif;
  }
  * { margin: 0; padding: 0; box-sizing: border-box; }
  html, body {
    width: 1200px; height: 1028px; overflow: hidden;
    background: var(--page);
  }
  .canvas { position: relative; width: 1200px; height: 1028px; }

  .card {
    position: absolute; left: 310px; width: 579px; height: 331px;
    box-shadow: 0 2px 5px rgba(0,0,0,0.18);
    overflow: hidden;
  }
  .card--front { top: 165px; background: var(--card); }
  .card--back  { top: 532px; background: var(--brand-blue); }

  /* Wordmark */
  .wordmark {
    position: absolute; display: flex; align-items: center;
    font-family: var(--serif); font-weight: 500; line-height: 0.92;
    letter-spacing: 0.01em;
  }
  .wordmark__dot { border-radius: 50%; flex: none; }
  .wordmark__name { display: flex; flex-direction: column; }

  .card--front .wordmark { left: 28px; top: 33px; color: var(--ink); font-size: 33px; gap: 10px; }
  .card--front .wordmark__dot { width: 30px; height: 30px; background: var(--brand-blue); }

  .card--back .wordmark {
    left: 0; right: 0; top: 0; bottom: 0; justify-content: center;
    color: #ffffff; font-size: 54px; gap: 16px;
  }
  .card--back .wordmark__dot { width: 48px; height: 48px; background: #ffffff; }

  .ghost-mark {
    position: absolute; left: 320px; top: 42px; width: 220px; height: 220px;
    border-radius: 50%; background: var(--ghost);
  }

  .holder { position: absolute; left: 28px; top: 178px; }
  .holder__name {
    font-family: var(--serif); font-weight: 500; font-size: 21px;
    color: var(--brand-blue); letter-spacing: 0.01em; line-height: 1;
  }
  .holder__title {
    font-family: var(--sans); font-size: 14px; color: var(--muted);
    margin-top: 6px; letter-spacing: 0.03em;
  }

  .rule {
    position: absolute; left: 28px; top: 228px; width: 522px; height: 2px;
    background: var(--brand-blue);
  }

  .contact {
    position: absolute; left: 28px; top: 244px; list-style: none;
    font-family: var(--sans); font-size: 14px; color: var(--muted);
    letter-spacing: 0.03em;
  }
  .contact li { display: flex; align-items: center; height: 20px; }
  .contact svg { width: 12px; height: 12px; margin-right: 10px; flex: none; }
  .contact .accent { color: var(--brand-blue); }

  .address {
    position: absolute; right: 29px; top: 264px; text-align: right;
    font-family: var(--sans); font-size: 14px; color: var(--muted);
    line-height: 20px; letter-spacing: 0.03em; font-style: normal;
  }
</style>
</head>
<body>
<main class="canvas">

  <section class="card card--front" aria-label="Card front">
    <div class="ghost-mark" aria-hidden="true"></div>

    <div class="wordmark">
      <span class="wordmark__dot" aria-hidden="true"></span>
      <span class="wordmark__name"><span>MERIDIAN</span><span>SPINE</span></span>
    </div>

    <div class="holder">
      <p class="holder__name">DANIEL MORROW</p>
      <p class="holder__title">Director</p>
    </div>

    <div class="rule"></div>

    <ul class="contact">
      <li>
        <svg viewBox="0 0 12 12" aria-hidden="true"><path d="M3 1 L4.6 1 L5.4 3.4 L4.2 4.4 Q5 6.8 7.4 8 L8.5 6.8 L11 7.6 L11 9.3 Q10.5 11 8.6 11 Q2.5 10 1 3.2 Q1.2 1.2 3 1 Z" fill="var(--brand-blue)"/></svg>
        (555) 318-2046
      </li>
      <li>
        <svg viewBox="0 0 12 12" aria-hidden="true"><rect x="1" y="2.5" width="10" height="7" fill="none" stroke="var(--brand-blue)" stroke-width="1.2"/><path d="M1 2.8 L6 6.6 L11 2.8" fill="none" stroke="var(--brand-blue)" stroke-width="1.2"/></svg>
        hello@meridianspine.com
      </li>
      <li>
        <svg viewBox="0 0 12 12" aria-hidden="true"><g fill="none" stroke="var(--brand-blue)" stroke-width="1"><circle cx="6" cy="6" r="5"/><ellipse cx="6" cy="6" rx="2.2" ry="5"/><path d="M1 6 H11 M1.8 3.5 H10.2 M1.8 8.5 H10.2"/></g></svg>
        <span>www.<span class="accent">meridianspine</span>.com</span>
      </li>
    </ul>

    <address class="address">1187 Larchmont Way<br>Salem, OR 97301</address>
  </section>

  <section class="card card--back" aria-label="Card back">
    <div class="wordmark">
      <span class="wordmark__dot" aria-hidden="true"></span>
      <span class="wordmark__name"><span>MERIDIAN</span><span>SPINE</span></span>
    </div>
  </section>

</main>
</body>
</html>
```